PAX

We need to design a power point presentation that can englobe all our company products.

This presentation has to have all the required to be used as template for future presentations.

We focus on prodcut developing for supermarkets, ( we help them with their own brand products ex. Sunny Harvest, TK, etc.)
Also we are on the marine industry, we develop ships and oil rigs for the Oil and deep water market.

Target Market(s)

Oil Companies
Supermarket companies
Retail Companies

Industry/Entity Type

It Company

Requirements
Must have
• Our Logo and company colors
Nice to have
• Something describing globalization.
Should not have
• Orange color

```html
<!DOCTYPE html>
<html lang="es">
<head>
<meta charset="utf-8">
<title>Nuestra Empresa</title>
<link href="https://fonts.googleapis.com/css2?family=Open+Sans:wght@300;400;600;700&display=swap" rel="stylesheet">
<style>
  :root {
    --blue: #1a9ad6;
    --blue-light: #6cc7f0;
    --navy: #1b2a55;
    --green: #7bc043;
    --text: #333333;
    --rule: #bcd6e6;
    --bg: #ffffff;
  }
  * { margin: 0; padding: 0; box-sizing: border-box; }
  html, body { width: 1200px; height: 900px; overflow: hidden; background: var(--bg); }
  body { font-family: "Open Sans", Arial, sans-serif; color: var(--text); }

  .slide { position: relative; width: 1200px; height: 900px; overflow: hidden; background: var(--bg); }

  .map-backdrop {
    position: absolute; inset: 0;
    background: radial-gradient(ellipse at 60% 40%, #f3f5f7 0%, #fafbfc 55%, #ffffff 100%);
  }

  .slide-header { position: absolute; left: 44px; top: 30px; width: 1110px; height: 70px; }
  .slide-title {
    position: absolute; left: 0; top: 4px;
    font-weight: 300; font-size: 38px; letter-spacing: 0.5px; color: var(--navy);
  }
  .review-tag {
    position: absolute; right: 0; top: 18px;
    font-weight: 400; font-size: 20px; color: var(--green);
  }
  .review-tag .year { font-weight: 700; color: var(--blue-light); }
  .header-rule { position: absolute; left: 0; top: 52px; }

  .content { position: absolute; left: 44px; width: 1130px; white-space: nowrap; }
  .lead {
    font-weight: 300; font-size: 25px; line-height: 30.5px;
    color: var(--blue); text-transform: uppercase;
  }
  .lead strong { font-weight: 700; }
  .body-copy {
    font-weight: 300; font-size: 19.4px; line-height: 26.4px; color: var(--text);
  }
  .body-copy strong { font-weight: 700; color: #111; }

  .intro-lead { top: 172px; }
  .intro-copy { top: 290px; }
  .section-divider {
    position: absolute; left: 44px; top: 424px; width: 392px; height: 1px; background: var(--rule);
  }
  .location-lead { top: 466px; }
  .location-copy { top: 518px; }

  .corner-tint {
    position: absolute; left: 0; top: 660px; width: 480px; height: 240px;
    background: linear-gradient(160deg, rgba(123,192,67,0.35) 0%, rgba(108,199,240,0.28) 45%, rgba(255,255,255,0) 85%);
  }

  .brand {
    position: absolute; left: 10px; top: 838px;
    font-weight: 600; font-size: 15px; line-height: 18px; color: var(--navy);
    letter-spacing: 0.5px;
  }
</style>
</head>
<body>
<div class="slide">
  <div class="map-backdrop" role="img" aria-label="Mapa mundial tenue de fondo"></div>

  <header class="slide-header">
    <h1 class="slide-title">NUESTRA EMPRESA</h1>
    <div class="review-tag">STRATEGIC REVIEW <span class="year">2014</span></div>
    <svg class="header-rule" width="1110" height="16" viewBox="0 0 1110 16">
      <polyline points="0,0.5 8,0.5 18,10 28,0.5 1110,0.5" fill="none" stroke="#5bbbe8" stroke-width="1.2"/>
    </svg>
  </header>

  <p class="content lead intro-lead">
    Está dedicada principalmente a brindar soluciones en el sector <strong>marítimo petrole-<br>ro, enfocándonos</strong> en productos de vanguardia que se adapten a las necesidades<br>en dicho sector.
  </p>

  <p class="content body-copy intro-copy">
    Buscamos la mejora continua de nuestros servicios, procesos y productos. Generamos sinergia de forma internacional,<br>acercando a las grandes corporaciones y empresas de <strong>CHINA,</strong> facilitando los procesos de incorporación de éstas al mer-<br>cado de exploración, producción, construcción, avituallamiento y mantenimiento marítimo del sector petrolero, en aguas<br>profundas y cuencas del sureste del <strong>GOLFO DE MÉXICO.</strong>
  </p>

  <div class="section-divider"></div>

  <p class="content lead location-lead">
    Al estar posicionados en <strong>Hong Kong y Beijing</strong>
  </p>

  <p class="content body-copy location-copy">
    Nos permite enlazar y trabajar con fabricantes y constructores&nbsp; que cubren las necesidades con estándares internacionales<br>de calidad y garantía a satisfacción del sector marítimo petrolero, garantizando y fortaleciendo la orientación para nuestros<br>clientes, en la gestión de las negociaciones y logrando que las operaciones sean seguras y confiables, maximizando así el<br>valor de las oportunidades.
  </p>

  <div class="corner-tint" role="img" aria-label="Acento decorativo en tonos verde y azul en la esquina inferior izquierda"></div>

  <div class="brand">NAVALIA<br>MARINE SOLUTIONS</div>
</div>
</body>
</html>
```